Bright Harbor Learning Center Brochure Design

We are looking for a visually appealing and well-structured tri-fold brochure that effectively communicates our mission, values, and offerings. The brochure should be engaging, informative, and eye-catching, ensuring that families can easily connect with our message.
Key Requirements:
- Front Cover: Must include our Bright Harbor Learning Center logo and a compelling design that draws attention.
- Back Panel: Should display our locations, social media handles, QR code, website, and phone number, arranged neatly for easy access. (Reference the attached example for layout inspiration.)
- Content & Imagery: The provided text must be incorporated in a clean, organized layout that flows naturally. We’ve also included photos of children we would like used. (Not all photos have to be used, just some)
- Design & Color Scheme: We are open to creative variations, but the overall aesthetic should feel cohesive, professional, and visually engaging. The design should capture the warmth, care, and discovery-based learning environment we provide.
- Attention-Grabbing & Readable: The brochure should be easy to read, with well-balanced text and imagery that doesn’t overwhelm the viewer.
We are excited to see your creative approach—make it stand out while maintaining clarity and professionalism!
---------------------------------------------------------------------------
This is the info that needs to be used:
Welcome to Bright Harbor Learning Center
Where Learning & Care Come Together!
At Bright Harbor, we go beyond childcare—we create a warm, nurturing community where families feel supported and confident in their child’s growth.
✅ Privately owned early learning centers with hands-on leadership
✅ Safe, engaging environments designed to inspire young minds
✅ Now transitioning to a Reggio Emilia-inspired approach—encouraging exploration, creativity, and child-led learning
We are also proud to offer exclusive corporate discounts for professionals in key industries:
🔹 Teachers
🔹 Healthcare & Hospital Staff
🔹 Law Enforcement & First Responders
🔹 Military Families
🔹 Employees of Partnered Businesses & Apartments
Quality childcare should be affordable and accessible—because when families thrive, communities grow!
Our Approach: Learning Through Exploration
At Bright Harbor, we believe that children learn best through curiosity, hands-on discovery, and meaningful experiences. That’s why we are transitioning to a Reggio Emilia-inspired philosophy, where:
✨ Children take the lead – Learning is shaped by their interests and natural curiosity
✨ Teachers are guides – Educators observe, support, and enrich children’s experiences
✨ The environment is a teacher – Classrooms are designed to inspire creativity and exploration
✨ Collaboration is key – Children, families, and educators work together in a connected learning community
We blend this philosophy with The Playwise Framework® for Preschool and Emergent Curriculum to create a research-backed, child-centered learning experience. The Playwise Framework® builds confidence, critical thinking, and academic readiness, while Emergent Curriculum adapts lessons to children's interests—making learning engaging, meaningful, and fun.
Our Mission: Growing Together
🌟 Building strong partnerships – Open communication with families & communities
🌟 Nurturing confidence & creativity – Every child is seen, heard, and supported
🌟 Fostering a lifelong love for learning – Through discovery, exploration & meaningful experiences
As we transition to a Reggio Emilia-inspired approach, we are excited to offer a learning experience that is more engaging, dynamic, and child-centered than ever before.
Imagine a place where every child’s voice is heard, creativity is celebrated, and learning is an adventure—welcome to Bright Harbor!

```html
<!DOCTYPE html>
<html lang="en">
<head>
<meta charset="utf-8">
<title>Bright Harbor Learning Center – Brochure Inside</title>
<link href="https://fonts.googleapis.com/css2?family=Fredoka:wght@600;700&family=Arimo:wght@400;700&family=Crimson+Text:ital@1&display=swap" rel="stylesheet">
<style>
  :root{
    --stage:#dedede;
    --paper:#ffffff;
    --mint:#d8e7df;
    --navy:#1f3f8f;
    --blue:#2f6fd0;
    --sky:#6bb8ea;
    --sky-pale:#a9d6f3;
    --green:#3aa63a;
    --check:#8ccf2a;
    --yellow:#f3ee3c;
    --pink:#f08aa8;
    --text-dark:#2a2a2a;
  }
  *{box-sizing:border-box;margin:0;padding:0}
  html,body{width:1200px;height:900px;overflow:hidden;background:var(--stage)}
  .brochure{position:absolute;left:42px;top:20px;width:1116px;height:860px;display:flex;box-shadow:0 6px 18px rgba(0,0,0,.18)}
  .panel{position:relative;width:372px;height:100%;overflow:hidden}
  .heading{font-family:"Fredoka",sans-serif;font-weight:700;line-height:1.02}
  .photo{position:absolute;background:linear-gradient(135deg,#c9a877,#e8d7b4)}

  /* left panel */
  .panel-left{background:var(--paper)}
  .panel-left .photo-top{left:36px;top:44px;width:270px;height:250px;border-radius:48% 52% 50% 50%;border-bottom:8px solid var(--sky-pale);background:linear-gradient(160deg,#d8c19a,#a8875a)}
  .panel-left .heading{position:absolute;left:34px;top:344px;width:310px;font-size:31px;color:var(--blue)}
  .panel-left .sub{position:absolute;left:34px;top:460px;width:310px;font-family:"Arimo",sans-serif;font-size:17px;color:var(--green);line-height:1.25}
  .panel-left .blob{position:absolute;left:40px;top:560px;width:420px;height:420px;border-radius:50%;background:var(--sky)}
  .panel-left .photo-bottom{left:0;top:590px;width:372px;height:270px;border-radius:0 60px 0 0;background:linear-gradient(160deg,#4f7fd6 0%,#f1c94a 45%,#e2b25c 100%)}

  /* middle panel */
  .panel-mid{background:var(--mint)}
  .brand{position:absolute;left:0;right:0;top:40px;text-align:center}
  .brand-mark{display:inline-block;width:22px;height:22px;border-radius:50%;background:var(--blue);vertical-align:middle;margin-right:8px}
  .brand-name{font-family:"Fredoka",sans-serif;font-weight:700;font-size:22px;color:var(--blue);vertical-align:middle}
  .panel-mid .heading{position:absolute;left:30px;top:100px;width:320px;font-size:31px;color:var(--navy)}
  .intro{position:absolute;left:30px;top:214px;width:318px;font-family:"Arimo",sans-serif;font-size:14.5px;color:var(--green);line-height:1.35}
  .pillars{position:absolute;left:30px;top:330px;width:318px;list-style:none}
  .pillars li{position:relative;padding-left:28px;margin-bottom:12px;font-family:"Fredoka",sans-serif;font-weight:600;font-size:14.5px;line-height:1.2;color:var(--navy)}
  .tick{position:absolute;left:0;top:1px;width:20px;height:18px}
  .blend{position:absolute;left:30px;top:560px;width:300px;font-family:"Crimson Text",serif;font-style:italic;font-size:14.5px;line-height:1.35;color:var(--text-dark);text-align:justify}
  .mid-curve{position:absolute;left:0;top:0;width:372px;height:860px}

  /* right panel */
  .panel-right{background:linear-gradient(180deg,var(--blue) 0%,#3f88db 45%,var(--sky) 100%)}
  .panel-right .heading{position:absolute;left:28px;top:40px;width:320px;font-size:30px;color:#fff}
  .mission{position:absolute;left:28px;top:124px;width:320px;list-style:none}
  .mission li{position:relative;padding-left:28px;margin-bottom:10px;font-family:"Fredoka",sans-serif;font-weight:600;font-size:13.5px;line-height:1.2;color:#fff}
  .transition{position:absolute;left:28px;top:268px;width:310px;font-family:"Crimson Text",serif;font-style:italic;font-size:14px;line-height:1.35;color:#fff}
  .panel-right .ring{position:absolute;left:20px;top:370px;width:400px;height:400px;border-radius:50%;background:var(--sky-pale)}
  .panel-right .photo-play{left:34px;top:384px;width:380px;height:380px;border-radius:50%;background:linear-gradient(150deg,#c7a57a 0%,#e97fa7 45%,#5fae4a 100%)}
  .callout{position:absolute;left:34px;top:720px;width:306px;padding:12px 14px;background:var(--yellow);border-radius:14px;font-family:"Fredoka",sans-serif;font-weight:600;font-size:14px;line-height:1.22;color:var(--blue)}
  .heart{position:absolute;width:20px;height:18px}
</style>
</head>
<body>
<main class="brochure">

  <section class="panel panel-left">
    <div class="photo photo-top" role="img" aria-label="Photo of a child exploring a sensory bin filled with grain"></div>
    <svg class="heart" style="left:300px;top:50px" viewBox="0 0 20 18"><path d="M10 17 1 8a5 5 0 0 1 9-5 5 5 0 0 1 9 5z" fill="var(--pink)"/></svg>
    <h2 class="heading">Quality childcare should be affordable and accessible</h2>
    <p class="sub">because when families thrive, communities grow!</p>
    <div class="blob"></div>
    <div class="photo photo-bottom" role="img" aria-label="Photo of children reading picture books together on cushions"></div>
  </section>

  <section class="panel panel-mid">
    <svg class="mid-curve" viewBox="0 0 372 860" aria-hidden="true">
      <path d="M372 520 Q300 560 300 700 Q300 820 200 860 L372 860Z" fill="var(--sky)"/>
      <path d="M372 540 Q318 580 318 700 Q318 830 220 860" fill="none" stroke="var(--sky-pale)" stroke-width="6"/>
    </svg>
    <div class="brand"><span class="brand-mark"></span><span class="brand-name">Bright Harbor</span></div>
    <h2 class="heading">Our Approach: Learning Through Exploration</h2>
    <p class="intro">At Bright Harbor, we believe that children learn best through curiosity, hands-on discovery, and meaningful experiences. That’s why we are transitioning to a Reggio Emilia-inspired philosophy, where:</p>
    <ul class="pillars">
      <li><svg class="tick" viewBox="0 0 20 18"><path d="M2 10l6 6L18 2" fill="none" stroke="var(--check)" stroke-width="4" stroke-linecap="round"/></svg>Children take the lead – Learning is shaped by their interests and natural curiosity</li>
      <li><svg class="tick" viewBox="0 0 20 18"><path d="M2 10l6 6L18 2" fill="none" stroke="var(--check)" stroke-width="4" stroke-linecap="round"/></svg>Teachers are guides – Educators observe, support, and enrich children’s experiences</li>
      <li><svg class="tick" viewBox="0 0 20 18"><path d="M2 10l6 6L18 2" fill="none" stroke="var(--check)" stroke-width="4" stroke-linecap="round"/></svg>The environment is a teacher – Classrooms are designed to inspire creativity and exploration</li>
      <li><svg class="tick" viewBox="0 0 20 18"><path d="M2 10l6 6L18 2" fill="none" stroke="var(--check)" stroke-width="4" stroke-linecap="round"/></svg>Collaboration is key – Children, families, and educators work together in a connected learning community</li>
    </ul>
    <p class="blend">We blend this philosophy with The Playwise Framework® for Preschool and Emergent Curriculum to create a research-backed, child-centered learning experience. The Playwise Framework® builds confidence, critical thinking, and academic readiness, while Emergent Curriculum adapts lessons to children’s interests—making learning engaging, meaningful, and fun.</p>
  </section>

  <section class="panel panel-right">
    <h2 class="heading">Our Mission:<br>Growing Together</h2>
    <ul class="mission">
      <li><svg class="tick" viewBox="0 0 20 18"><path d="M2 10l6 6L18 2" fill="none" stroke="var(--check)" stroke-width="4" stroke-linecap="round"/></svg>Building strong partnerships – Open communication with families &amp; communities</li>
      <li><svg class="tick" viewBox="0 0 20 18"><path d="M2 10l6 6L18 2" fill="none" stroke="var(--check)" stroke-width="4" stroke-linecap="round"/></svg>Nurturing confidence &amp; creativity – Every child is seen, heard, and supported</li>
      <li><svg class="tick" viewBox="0 0 20 18"><path d="M2 10l6 6L18 2" fill="none" stroke="var(--check)" stroke-width="4" stroke-linecap="round"/></svg>Fostering a lifelong love for learning – Through discovery, exploration &amp; meaningful experiences</li>
    </ul>
    <p class="transition">As we transition to a Reggio Emilia-inspired approach, we are excited to offer a learning experience that is more engaging, dynamic, and child-centered than ever before.</p>
    <svg class="heart" style="left:40px;top:380px" viewBox="0 0 20 18"><path d="M10 17 1 8a5 5 0 0 1 9-5 5 5 0 0 1 9 5z" fill="var(--pink)"/></svg>
    <div class="ring"></div>
    <div class="photo photo-play" role="img" aria-label="Photo of children playing together at an outdoor water and sand table"></div>
    <p class="callout">Imagine a place where every child’s voice is heard, creativity is celebrated, and learning is an adventure—welcome to Bright Harbor!</p>
  </section>

</main>
</body>
</html>
```